Business Card Design Project

Business card based on attached logo

Todd Merrick
Todd@lorvantest.com
877-514-9073 ext. 318
Www.LorvanTest.com

Industry/Entity Type

Business

```html
<!DOCTYPE html>
<html lang="en">
<head>
<meta charset="utf-8">
<title>LorvanTest Business Cards</title>
<link rel="stylesheet" href="https://fonts.googleapis.com/css2?family=Saira:wght@400;500;700;800&display=swap">
<style>
  :root {
    --brand-red: #ec1c24;
    --brand-black: #231f20;
    --paper: #ffffff;
    --backdrop: #e9e6e2;
    --ink: #231f20;
  }
  * { margin: 0; padding: 0; box-sizing: border-box; }
  html, body { width: 1200px; height: 716px; overflow: hidden; }
  body {
    background: var(--backdrop);
    font-family: "Saira", Arial, sans-serif;
    position: relative;
  }
  .card {
    position: absolute;
    width: 507px;
    height: 289px;
    overflow: hidden;
    box-shadow: 0 1px 3px rgba(0,0,0,0.25);
  }
  .card--front { left: 52px; top: 37px; background: var(--paper); }
  .card--white { left: 623px; top: 37px; background: var(--paper); }
  .card--red   { left: 48px; top: 379px; background: var(--brand-red); }
  .card--black { left: 629px; top: 381px; background: var(--brand-black); }

  /* Front card */
  .wordmark {
    position: absolute;
    left: 34px;
    top: 40px;
    display: flex;
    align-items: center;
    gap: 12px;
  }
  .wordmark__name {
    font-weight: 800;
    font-size: 52px;
    line-height: 1;
    color: var(--ink);
    letter-spacing: -1px;
  }
  .wordmark__square {
    width: 26px;
    height: 26px;
    background: var(--brand-red);
  }
  .contact {
    position: absolute;
    left: 34px;
    top: 177px;
    list-style: none;
    font-size: 12.5px;
    color: var(--ink);
  }
  .contact li {
    display: flex;
    align-items: center;
    gap: 7px;
    height: 23.5px;
  }
  .contact svg { width: 10px; height: 10px; fill: var(--brand-red); }
  .swoosh { position: absolute; left: 0; top: 0; width: 507px; height: 289px; }
  .holder-name {
    position: absolute;
    right: 22px;
    bottom: 11px;
    color: var(--paper);
    font-weight: 700;
    font-size: 19px;
    letter-spacing: 2px;
  }

  /* Back cards */
  .back-mark {
    position: absolute;
    left: 0; right: 0;
    top: 96px;
    display: flex;
    justify-content: center;
    align-items: center;
    gap: 14px;
  }
  .back-mark__name {
    font-weight: 800;
    font-size: 58px;
    line-height: 1;
    letter-spacing: -1px;
  }
  .back-mark__square { width: 30px; height: 30px; }
  .card--white .back-mark__name { color: var(--brand-red); }
  .card--white .back-mark__square { background: var(--brand-black); }
  .card--red .back-mark__name,
  .card--black .back-mark__name { color: var(--paper); }
  .card--red .back-mark__square { background: var(--brand-black); }
  .card--black .back-mark__square { background: var(--brand-red); }

  .back-url {
    position: absolute;
    left: 0; right: 0;
    bottom: 20px;
    text-align: center;
    font-size: 15px;
    letter-spacing: 2.4px;
  }
  .card--white .back-url { color: var(--ink); }
  .card--red .back-url,
  .card--black .back-url { color: var(--paper); }
</style>
</head>
<body>

  <section class="card card--front">
    <div class="wordmark">
      <span class="wordmark__name">LorvanTest</span>
      <span class="wordmark__square"></span>
    </div>

    <ul class="contact">
      <li>
        <svg viewBox="0 0 10 10"><path d="M2 0.5 L4 2.8 L3 4 C3.6 5.4 4.6 6.4 6 7 L7.2 6 L9.5 8 L8.2 9.5 C4.5 9.3 0.7 5.5 0.5 1.8Z"/></svg>
        <span>877-514-9073 ext. 318</span>
      </li>
      <li>
        <svg viewBox="0 0 10 10"><path d="M0 2.5 H10 V8.5 H0Z M0.6 2.9 L5 6 L9.4 2.9" fill="var(--brand-red)"/><path d="M0.8 3.1 L5 5.9 L9.2 3.1" stroke="#fff" stroke-width="0.8" fill="none"/></svg>
        <span>Todd@lorvantest.com</span>
      </li>
      <li>
        <svg viewBox="0 0 10 10"><circle cx="5" cy="5" r="4.3" fill="none" stroke="var(--brand-red)" stroke-width="1"/><path d="M0.8 5 H9.2 M5 0.8 V9.2" stroke="var(--brand-red)" stroke-width="0.8"/><ellipse cx="5" cy="5" rx="2" ry="4.3" fill="none" stroke="var(--brand-red)" stroke-width="0.8"/></svg>
        <span>www.LorvanTest.com</span>
      </li>
    </ul>

    <svg class="swoosh" viewBox="0 0 507 289" aria-hidden="true">
      <path d="M0 262 C110 252 230 232 340 222 C420 215 470 218 507 224 L507 240 C420 233 300 244 170 262 C110 270 50 276 0 280Z" fill="var(--brand-black)"/>
      <path d="M165 280 C260 258 370 232 470 222 C490 220 500 220 507 221 L507 224 C430 226 330 250 190 280Z" fill="var(--brand-red)"/>
      <path d="M0 280 C60 276 120 270 180 262 C300 246 420 236 507 240 L507 289 L0 289Z" fill="var(--brand-red)"/>
    </svg>

    <div class="holder-name">Todd Merrick</div>
  </section>

  <section class="card card--white">
    <div class="back-mark">
      <span class="back-mark__name">LorvanTest</span>
      <span class="back-mark__square"></span>
    </div>
    <div class="back-url">www.LorvanTest.com</div>
  </section>

  <section class="card card--red">
    <div class="back-mark">
      <span class="back-mark__name">LorvanTest</span>
      <span class="back-mark__square"></span>
    </div>
    <div class="back-url">www.LorvanTest.com</div>
  </section>

  <section class="card card--black">
    <div class="back-mark">
      <span class="back-mark__name">LorvanTest</span>
      <span class="back-mark__square"></span>
    </div>
    <div class="back-url">www.LorvanTest.com</div>
  </section>

</body>
</html>
```